Heron Loan Partners Business Card

We need a business card design for our mortgage servicing company. In addition to servicing the loans of homeowners, we help homeowners with purchasing their homes and any mortgage refinancing. We would like to see designs that use the colors in the logo attached below (gold-ish yellow and navy blue), and any other design you deem fit! The design should communicate a simpler life with smart mortgages provided by Heron.

```html
<!DOCTYPE html>
<html lang="en">
<head>
<meta charset="utf-8">
<title>Heron Loan Partners – Business Card</title>
<link rel="stylesheet" href="https://fonts.googleapis.com/css2?family=Open+Sans:wght@400;700&display=swap">
<style>
  :root {
    --backdrop: #2b2b2e;
    --navy: #241f55;
    --navy-deep: #16123b;
    --gold: #e2ad33;
    --white: #ffffff;
  }
  * { margin: 0; padding: 0; box-sizing: border-box; }
  html, body {
    width: 1200px; height: 780px; overflow: hidden;
    background: var(--backdrop);
    font-family: "Open Sans", Arial, sans-serif;
  }
  .sheet {
    width: 1200px; height: 780px;
    display: flex; align-items: center; justify-content: center; gap: 36px;
  }
  .card {
    position: relative;
    width: 560px; height: 320px;
    background: var(--navy);
    border-radius: 3px;
    overflow: hidden;
  }
  .brand-name {
    font-weight: 700;
    color: var(--navy-deep);
    letter-spacing: 0.5px;
  }
  .card-front { display: flex; align-items: center; justify-content: center; }
  .card-front .brand-name { font-size: 40px; }

  .card-back .brand-name {
    position: absolute; left: 28px; top: 26px; font-size: 20px;
  }
  .contact {
    position: absolute; right: 44px; top: 150px;
    text-align: right; color: var(--white);
  }
  .person-name {
    font-size: 29px; font-weight: 700; color: var(--gold);
    line-height: 1.1; letter-spacing: 0.5px;
  }
  .person-role { font-size: 14px; margin-bottom: 6px; }
  .address { font-size: 13px; line-height: 1.35; margin-bottom: 4px; }
  .contact-line {
    display: flex; align-items: center; justify-content: flex-end; gap: 8px;
    font-size: 13px; line-height: 1.45;
  }
  .contact-line svg { width: 13px; height: 13px; fill: var(--gold); flex: none; }
  .gold-tab {
    position: absolute; right: 0; top: 150px;
    width: 22px; height: 44px; background: var(--gold);
  }
</style>
</head>
<body>
<main class="sheet">
  <section class="card card-front">
    <span class="brand-name">Heron Loan Partners</span>
  </section>

  <section class="card card-back">
    <span class="brand-name">Heron Loan Partners</span>
    <div class="gold-tab"></div>
    <div class="contact">
      <p class="person-name">Delia Raskin</p>
      <p class="person-role">Co-Founder</p>
      <p class="address">418 Lakeshore Ave. Suite 300<br>Denton, TX 76201</p>
      <p class="contact-line">(940) 555-0182
        <svg viewBox="0 0 24 24" aria-hidden="true"><path d="M6.6 10.8a15.1 15.1 0 0 0 6.6 6.6l2.2-2.2a1 1 0 0 1 1-.25 11.4 11.4 0 0 0 3.6.57 1 1 0 0 1 1 1V20a1 1 0 0 1-1 1A17 17 0 0 1 3 4a1 1 0 0 1 1-1h3.5a1 1 0 0 1 1 1c0 1.25.2 2.45.57 3.57a1 1 0 0 1-.25 1z"/></svg>
      </p>
      <p class="contact-line">hello@heronloan.com
        <svg viewBox="0 0 24 24" aria-hidden="true"><path d="M3 5h18a1 1 0 0 1 1 1v12a1 1 0 0 1-1 1H3a1 1 0 0 1-1-1V6a1 1 0 0 1 1-1zm9 7.5L4 7.3V8l8 5.2L20 8v-.7z"/></svg>
      </p>
      <p class="contact-line">www.heronloan.com
        <svg viewBox="0 0 24 24" aria-hidden="true"><path d="M12 2a10 10 0 1 0 0 20 10 10 0 0 0 0-20zm6.9 6h-3a15.6 15.6 0 0 0-1.4-3.6A8 8 0 0 1 18.9 8zM12 4a14 14 0 0 1 1.9 4h-3.8A14 14 0 0 1 12 4zM4.3 14a8.2 8.2 0 0 1 0-4h3.4a16.5 16.5 0 0 0 0 4zm.8 2h3a15.6 15.6 0 0 0 1.4 3.6A8 8 0 0 1 5.1 16zm3-8h-3a8 8 0 0 1 4.4-3.6A15.6 15.6 0 0 0 8.1 8zM12 20a14 14 0 0 1-1.9-4h3.8A14 14 0 0 1 12 20zm2.3-6H9.7a14.7 14.7 0 0 1 0-4h4.6a14.7 14.7 0 0 1 0 4zm.2 5.6a15.6 15.6 0 0 0 1.4-3.6h3a8 8 0 0 1-4.4 3.6zM16.3 14a16.5 16.5 0 0 0 0-4h3.4a8.2 8.2 0 0 1 0 4z"/></svg>
      </p>
    </div>
  </section>
</main>
</body>
</html>
```